Card Design for my dog training business Brightpaw Obedience

Need a business card design for my dog training business with my new logo. Want the card to come off professional yet fun. Want it to be very eye catchy as well. I normally have these at vet clinics, pet stores, and groomers. so need it to look better than my competitors.
Target Market(s)
dog owners
Industry/Entity Type
Dog Training
Contact Information for Business Card
needs logo, my name and info
Font styles to use
Serif
Colors
0255a3
ffffff
ec1f27
000000
333333
fbfbfb
Requirements
Must have
- Brightpaw Obedience
- Felix Orland
- 415 903 2276
- info@brightpawobedience.example
- www.brightpawobedience.example

```html
<!DOCTYPE html>
<html lang="en">
<head>
<meta charset="utf-8">
<title>Brightpaw Obedience – Business Card</title>
<link rel="stylesheet" href="https://fonts.googleapis.com/css2?family=Crimson+Text:wght@400;700&display=swap">
<style>
  :root {
    --backdrop: #2b2d31;
    --card-blue: #07608a;
    --card-white: #fbfbfb;
    --ink-white: #ffffff;
    --ink-dark: #333333;
    --brand-teal: #1a7aa0;
    --icon-blue: #07608a;
  }
  * { box-sizing: border-box; margin: 0; padding: 0; }
  html, body {
    width: 1200px; height: 900px; overflow: hidden;
    background: var(--backdrop);
    font-family: "Crimson Text", Georgia, serif;
  }
  .canvas {
    position: relative; width: 1200px; height: 900px;
    display: flex; align-items: center; justify-content: center; gap: 60px;
  }
  .card {
    position: relative; width: 520px; height: 297px;
    box-shadow: 0 14px 30px rgba(0,0,0,.45);
  }
  /* Front */
  .card--front { background: var(--card-blue); color: var(--ink-white); }
  .front__brand {
    position: absolute; left: 30px; top: 0; width: 190px; height: 100%;
    display: flex; align-items: center; justify-content: center; gap: 10px;
  }
  .brand-mark {
    width: 14px; height: 14px; border-radius: 50%; background: var(--ink-white); flex: none;
  }
  .brand-name {
    font-size: 26px; line-height: 1.1; font-weight: 400; color: var(--ink-white);
  }
  .front__details {
    position: absolute; left: 236px; top: 72px; right: 20px;
  }
  .person__name {
    font-size: 19px; font-weight: 700; letter-spacing: .04em; text-transform: uppercase;
  }
  .person__role { font-size: 15px; margin-bottom: 18px; }
  .contact-list { list-style: none; }
  .contact-list li {
    display: flex; align-items: center; gap: 9px;
    font-size: 15px; line-height: 1; margin-bottom: 11px; white-space: nowrap;
  }
  .contact-icon { width: 16px; height: 16px; flex: none; }
  /* Back */
  .card--back { background: var(--card-white); }
  .back__brand {
    position: absolute; left: 0; right: 0; top: 100px;
    display: flex; align-items: center; justify-content: center; gap: 10px;
  }
  .back__brand .brand-mark { background: var(--brand-teal); }
  .back__brand .brand-name { color: var(--brand-teal); font-size: 28px; }
  .back__web {
    position: absolute; left: 78px; bottom: 38px;
    font-size: 15px; font-weight: 700; color: var(--ink-dark);
  }
</style>
</head>
<body>
<main class="canvas">
  <section class="card card--front" aria-label="Card front">
    <div class="front__brand">
      <span class="brand-mark"></span>
      <span class="brand-name">Brightpaw Obedience</span>
    </div>
    <div class="front__details">
      <p class="person__name">Felix Orland</p>
      <p class="person__role">Owner</p>
      <ul class="contact-list">
        <li>
          <svg class="contact-icon" viewBox="0 0 16 16" aria-hidden="true">
            <circle cx="8" cy="8" r="8" fill="#fff"/>
            <path d="M5.2 4.2l1.6 1.6-.9 1.1c.5 1.1 1.4 2 2.5 2.5l1.1-.9 1.6 1.6-.9 1.3C7.7 11.2 4.8 8.3 4 5.1z" fill="var(--icon-blue)"/>
          </svg>
          415 903 2276
        </li>
        <li>
          <svg class="contact-icon" viewBox="0 0 16 16" aria-hidden="true">
            <circle cx="8" cy="8" r="8" fill="#fff"/>
            <rect x="4" y="5.2" width="8" height="5.6" fill="none" stroke="var(--icon-blue)" stroke-width="1"/>
            <path d="M4 5.4l4 3 4-3" fill="none" stroke="var(--icon-blue)" stroke-width="1"/>
          </svg>
          info@brightpawobedience.example
        </li>
        <li>
          <svg class="contact-icon" viewBox="0 0 16 16" aria-hidden="true">
            <circle cx="8" cy="8" r="8" fill="#fff"/>
            <circle cx="8" cy="8" r="4" fill="none" stroke="var(--icon-blue)" stroke-width="1"/>
            <ellipse cx="8" cy="8" rx="1.7" ry="4" fill="none" stroke="var(--icon-blue)" stroke-width="1"/>
            <path d="M4 8h8" stroke="var(--icon-blue)" stroke-width="1"/>
          </svg>
          www.brightpawobedience.example
        </li>
      </ul>
    </div>
  </section>

  <section class="card card--back" aria-label="Card back">
    <div class="back__brand">
      <span class="brand-mark"></span>
      <span class="brand-name">Brightpaw Obedience</span>
    </div>
    <p class="back__web">www.brightpawobedience.example</p>
  </section>
</main>
</body>
</html>
```